Refresh of graphic design for existing website

We would like to refresh our website. Please see the attached design specifications.

Industry/Entity Type

Graphic Design

```html
<!DOCTYPE html>
<html lang="en">
<head>
<meta charset="utf-8">
<title>The Garage Tool Alliance</title>
<link href="https://fonts.googleapis.com/css2?family=Open+Sans:wght@400;600;700&display=swap" rel="stylesheet">
<style>
:root{
  --green:#1f8a3e;
  --green-dark:#17702f;
  --blue:#2a62a6;
  --blue-dark:#1e4a80;
  --navy:#203f66;
  --ink:#2f3b4a;
  --muted:#6b7685;
  --line:#dde3ea;
  --panel:#f3f5f8;
  --white:#ffffff;
}
*{box-sizing:border-box;margin:0;padding:0}
html,body{width:818px;height:1200px;overflow:hidden}
body{font-family:"Open Sans",Arial,sans-serif;color:var(--ink);background:var(--white);font-size:10px;line-height:1.5}

.site-header{height:112px;position:relative;padding:18px 22px}
.brand{display:flex;align-items:center;gap:10px}
.brand-dot{width:44px;height:44px;border-radius:50%;background:var(--blue)}
.brand-name{font-size:24px;font-weight:700;color:var(--green)}
.site-title{position:absolute;left:22px;top:10px;font-size:15px;font-weight:700;color:var(--blue-dark)}
.site-header .brand{margin-top:26px}

.signin{position:absolute;right:14px;top:4px;width:186px;background:var(--blue-dark);color:var(--white);padding:8px 10px;border-radius:3px}
.signin h3{font-size:10px;font-weight:600;margin-bottom:5px}
.signin .field{height:14px;background:var(--white);border-radius:2px;margin-bottom:4px;color:#9aa4b0;font-size:7px;padding:1px 5px}
.signin .row{display:flex;justify-content:space-between;align-items:center;font-size:7px}
.signin .btn{background:var(--green);padding:1px 8px;border-radius:2px;font-size:7px}

.main-nav{height:32px;background:var(--green);display:flex;align-items:center;padding-left:60px}
.main-nav a{color:var(--white);text-decoration:none;font-size:9px;font-weight:600;padding:0 10px;line-height:32px}
.main-nav a.active{background:var(--green-dark)}

.hero{position:relative;height:356px;background:linear-gradient(120deg,#3a4a5c,#6b7a86 45%,#8b6f5a 70%,#3c4450)}
.hero-caption{position:absolute;left:28px;bottom:32px;width:280px;color:var(--white);font-size:9.5px;line-height:1.55}
.hero-arrow{position:absolute;top:160px;width:24px;height:24px;border-radius:50%;background:rgba(0,0,0,.45)}
.hero-arrow.prev{left:8px}.hero-arrow.next{right:8px}
.hero-arrow svg{display:block;margin:6px}

.tagline{height:46px;background:var(--blue);display:flex;align-items:center;justify-content:space-between;padding:0 30px}
.tagline p{color:var(--white);font-size:15px;font-weight:600}
.social{display:flex;gap:6px}
.social span{width:16px;height:16px;border-radius:50%;background:var(--white);opacity:.9}
.social span:nth-child(1){background:#3ab0e2}.social span:nth-child(2){background:#3b5b98}.social span:nth-child(3){background:#d34836}.social span:nth-child(4){background:#1f79b5}

.welcome{padding:22px 30px 12px}
.welcome h1{font-size:19px;font-weight:600;color:var(--blue-dark);margin-bottom:10px}
.welcome p{font-size:9.5px;color:var(--muted);margin-bottom:10px;line-height:1.6}

.columns{display:flex;gap:22px;padding:8px 30px 0}
.card{flex:1;height:304px;border:1px solid var(--line);background:var(--white);position:relative}
.card h2{height:28px;background:var(--blue);color:var(--white);font-size:12px;font-weight:600;text-align:center;line-height:28px}
.card .more{position:absolute;right:10px;bottom:8px;font-size:8px;font-weight:700;color:var(--blue)}

.event{display:flex;gap:8px;padding:10px 10px 4px}
.event .thumb{width:44px;height:44px;flex:none;background:linear-gradient(135deg,#7b8796,#b6a58e)}
.event h4{font-size:8.5px;font-weight:700;color:var(--blue-dark)}
.event p{font-size:7.5px;color:var(--muted);line-height:1.4}

.news{padding:8px 12px}
.news-item{border-bottom:1px solid var(--line);padding:6px 0 7px}
.news-item .date{font-size:7.5px;font-weight:700;color:var(--blue)}
.news-item p{font-size:7.5px;color:var(--muted);line-height:1.4}

.links{list-style:none;padding:10px 12px}
.links li{display:flex;align-items:center;gap:6px;font-size:8.5px;color:var(--ink);padding:3.5px 0;border-bottom:1px dotted var(--line)}

.site-footer{position:absolute;left:0;top:1128px;width:818px;height:72px;background:var(--navy);color:#c9d4e3;padding:16px 30px;font-size:8.5px}
.site-footer .top-link{position:absolute;right:30px;top:18px}
</style>
</head>
<body>
<header class="site-header">
  <div class="site-title">The Garage Tool Alliance</div>
  <div class="brand"><span class="brand-dot"></span><span class="brand-name">GTA</span></div>
  <form class="signin">
    <h3>Sign in to your account</h3>
    <div class="field">Username</div>
    <div class="field">Password</div>
    <div class="row"><span>Remember me</span><span class="btn">Login</span></div>
    <div class="row"><span>Forgot password?</span></div>
  </form>
</header>

<nav class="main-nav">
  <a class="active">HOME</a><a>ABOUT</a><a>MEMBERSHIP</a><a>GTA MEMBERS</a><a>GTA EVENTS</a><a>TOOLDOC LIBRARY</a><a>MARKET RESEARCH</a><a>MEMBER FILES</a>
</nav>

<section class="hero" role="img" aria-label="Photo of two technicians working together on vehicle service equipment in a workshop">
  <span class="hero-arrow prev"><svg width="12" height="12" viewBox="0 0 12 12"><path d="M8 2 4 6l4 4" stroke="#fff" stroke-width="2" fill="none"/></svg></span>
  <span class="hero-arrow next"><svg width="12" height="12" viewBox="0 0 12 12"><path d="M4 2l4 4-4 4" stroke="#fff" stroke-width="2" fill="none"/></svg></span>
  <p class="hero-caption">GTA's mission is to advance the vehicle service industry by providing technical data and open dialog between the manufacturers of transportation products, government regulators and the providers of tools, equipment and service information.</p>
</section>

<div class="tagline">
  <p>Advancing the vehicle service industry since 1947</p>
  <div class="social"><span></span><span></span><span></span><span></span></div>
</div>

<section class="welcome">
  <h1>Welcome to The Garage Tool Alliance</h1>
  <p>GTA is one of the most respected trade associations in the automotive aftermarket, giving fair and equitable representation to all segments of the equipment and tool industry. The Alliance is an association of automotive tool and equipment manufacturers and technical information providers and existing organizations.</p>
  <p>GTA's mission is to advance the vehicle service industry by providing technical data and open dialog between the manufacturers of transportation products, government regulators and the providers of tools, equipment and service information.</p>
</section>

<div class="columns">
  <section class="card">
    <h2>Upcoming Events</h2>
    <div class="event"><div class="thumb" role="img" aria-label="Event photo"></div><div><h4>EQUIPMENT &amp; TOOLS</h4><p>Posted on 15 Aug 2015<br>Short summary of the member event and its agenda.</p></div></div>
    <div class="event"><div class="thumb" role="img" aria-label="Event photo"></div><div><h4>EQUIPMENT &amp; TOOLS</h4><p>Posted on 15 Aug 2015<br>Short summary of the member event and its agenda.</p></div></div>
    <div class="event"><div class="thumb" role="img" aria-label="Event photo"></div><div><h4>EQUIPMENT &amp; TOOLS</h4><p>Posted on 15 Aug 2015<br>Short summary of the member event and its agenda.</p></div></div>
    <span class="more">[ READ MORE ]</span>
  </section>
  <section class="card">
    <h2>News Feed</h2>
    <div class="news">
      <div class="news-item"><div class="date">Sept 10th 2015</div><p>Brief industry update on service tools and new member news.</p></div>
      <div class="news-item"><div class="date">Sept 10th 2015</div><p>Brief industry update on service tools and new member news.</p></div>
      <div class="news-item"><div class="date">Sept 10th 2015</div><p>Brief industry update on service tools and new member news.</p></div>
      <div class="news-item"><div class="date">Sept 10th 2015</div><p>Brief industry update on service tools and new member news.</p></div>
    </div>
    <span class="more">[ READ MORE ]</span>
  </section>
  <section class="card">
    <h2>Quick Links</h2>
    <ul class="links">
      <li><svg width="8" height="8" viewBox="0 0 8 8"><path d="M1 4l2 2 4-5" stroke="#1f8a3e" stroke-width="1.5" fill="none"/></svg>ToolDoc Library</li>
      <li><svg width="8" height="8" viewBox="0 0 8 8"><path d="M1 4l2 2 4-5" stroke="#1f8a3e" stroke-width="1.5" fill="none"/></svg>GTA News Blog</li>
      <li><svg width="8" height="8" viewBox="0 0 8 8"><path d="M1 4l2 2 4-5" stroke="#1f8a3e" stroke-width="1.5" fill="none"/></svg>GTA Member Companies</li>
      <li><svg width="8" height="8" viewBox="0 0 8 8"><path d="M1 4l2 2 4-5" stroke="#1f8a3e" stroke-width="1.5" fill="none"/></svg>GTA Archive Publications</li>
      <li><svg width="8" height="8" viewBox="0 0 8 8"><path d="M1 4l2 2 4-5" stroke="#1f8a3e" stroke-width="1.5" fill="none"/></svg>Government Reporting Guide</li>
      <li><svg width="8" height="8" viewBox="0 0 8 8"><path d="M1 4l2 2 4-5" stroke="#1f8a3e" stroke-width="1.5" fill="none"/></svg>GTA Market Research Surveys</li>
      <li><svg width="8" height="8" viewBox="0 0 8 8"><path d="M1 4l2 2 4-5" stroke="#1f8a3e" stroke-width="1.5" fill="none"/></svg>Proposed Events</li>
      <li><svg width="8" height="8" viewBox="0 0 8 8"><path d="M1 4l2 2 4-5" stroke="#1f8a3e" stroke-width="1.5" fill="none"/></svg>Share Your News</li>
      <li><svg width="8" height="8" viewBox="0 0 8 8"><path d="M1 4l2 2 4-5" stroke="#1f8a3e" stroke-width="1.5" fill="none"/></svg>Tool Program Update</li>
      <li><svg width="8" height="8" viewBox="0 0 8 8"><path d="M1 4l2 2 4-5" stroke="#1f8a3e" stroke-width="1.5" fill="none"/></svg>Member Procedures</li>
      <li><svg width="8" height="8" viewBox="0 0 8 8"><path d="M1 4l2 2 4-5" stroke="#1f8a3e" stroke-width="1.5" fill="none"/></svg>Good Start</li>
    </ul>
    <span class="more">[ READ MORE ]</span>
  </section>
</div>

<footer class="site-footer">
  <p>GTA · 4100 Harbor Way, Suite 310, Lakeview, MI 48000 · 555-014-2290</p>
  <p>Copyright © 2015 The Garage Tool Alliance. All rights reserved.</p>
  <span class="top-link">TOP ▲</span>
</footer>
</body>
</html>
```